KVR Inc Web Design

WHAT ARE WE DOING?
We are developing a new website look and feel for a new company called KVR Inc. This new look and feel should include colors, design elements, choice of photography and other imagery, fonts, and other user experience elements.

WHAT DO THEY DO?
KVR, Inc, makes tools for researchers who are studying protein-protein interactions. These molecules are the basic tools of biology, and serve as key targets for drug developers and disease researchers. The world of proteins is enormously complex, and companies like KVR provide researchers with critical tools that help them elucidate this world.

WHO ARE WE TALKING TO?
The target audience for this website are professional scientists working in university research or biopharma drug development. They are highly sophisticated consumers looking for key tools that will advance their research.

WHAT DO WE WANT THEM TO DO?
The site is an information resource for the customer exploring the tools that KVR sells and the scientific issues surrounding protein-protein interactions. They should be able to navigate easily to their content of choice, while the whole site should convey a professionalism that enhanced KVR’s credibility.

WHAT DOES THE KVR BRAND STAND FOR?
KVR stands for illumination. Proteins are challenging to study, and KVR exists to help shed light on their workings.

WHAT ARE THE KEY VALUES OF THE KVR BRAND?
Integrity. Innovation. Insight.

WHAT ARE THE EXECUTIONAL MANDITORIES?
The look and feel is completely up for grabs. Nothing is off the table.

WHAT ARE THE DELIVERABLES?
We need new designs for the following templates:
http://cms.marlowbench.com/
http://cms.marlowbench.com/products-and-services/instruments-3/bench-top-instruments/
http://cms.marlowbench.com/category/lab-study/

```html
<!DOCTYPE html>
<html lang="en">
<head>
<meta charset="utf-8">
<title>KVR Inc — Bench Top Instruments</title>
<link href="https://fonts.googleapis.com/css2?family=Roboto:wght@300;400;500&display=swap" rel="stylesheet">
<style>
:root{
  --orange:#f3a521;
  --text:#333;
  --brand:#555;
  --nav:#8a8a8a;
  --rule:#bdbdbd;
  --tab:#c6c6c6;
  --panel:#f3f3f3;
  --panel-border:#dedede;
  --footer:#3b3b3b;
  --hero-a:#7fa9d8;
  --hero-b:#2f5e9e;
  --dark-btn:#4a4a4a;
}
*{box-sizing:border-box;margin:0;padding:0}
html,body{width:936px;height:1200px;overflow:hidden;background:#fff}
body{font-family:'Roboto',sans-serif;color:var(--text);position:relative}
.site-header{position:absolute;top:0;left:0;width:936px;height:86px}
.brand{position:absolute;left:102px;top:32px;font-size:28px;font-weight:400;line-height:32px;color:var(--brand)}
.search{position:absolute;left:686px;top:7px;width:138px;height:20px;border:1px solid #d6d6d6;font-size:8px;color:#999;padding:5px 6px}
.search svg{position:absolute;right:4px;top:4px}
.main-nav{position:absolute;right:110px;top:39px;font-size:14px;font-weight:300;color:var(--nav);white-space:nowrap}
.main-nav .active{color:var(--orange)}
.hero{position:absolute;top:86px;left:0;width:936px;height:398px;background:linear-gradient(100deg,var(--hero-a),var(--hero-b) 45%,#9bb8dc 75%,#dfe7f1)}
.hero-dots{position:absolute;left:434px;top:441px;display:flex;gap:4px}
.hero-dots span{width:14px;height:14px;border-radius:50%;background:#444}
.hero-dots span.on{background:var(--orange)}
.section-title{position:absolute;left:102px;top:505px;font-size:18px;font-weight:500;color:#222}
.section-sub{position:absolute;left:102px;top:538px;font-size:14px;font-weight:300;color:var(--orange)}
.pager{position:absolute;left:795px;top:537px;display:flex;gap:4px}
.section-rule{position:absolute;left:102px;top:564px;width:733px;border-top:1px solid var(--rule)}
.feature-photo{position:absolute;left:102px;top:577px;width:270px;height:180px;background:linear-gradient(135deg,#c9d6e6,#e8eef5 50%,#9fb3cc)}
.feature-copy{position:absolute;left:386px;top:574px;width:452px;font-size:14px;font-weight:300;line-height:18.8px;letter-spacing:-0.25px;color:#222}
.feature-copy p{margin-bottom:18.8px}
.feature-copy a{color:var(--orange);text-decoration:none;font-weight:400}
.tabs{position:absolute;left:101px;top:788px;height:44px}
.tab{position:absolute;top:0;height:44px;font-size:14px;font-weight:400;color:#fff;background:var(--tab);display:flex;align-items:center;justify-content:center}
.tab.current{background:#f7f7f7;color:#222;border:1px solid var(--panel-border);border-bottom:none;height:45px;z-index:2}
.tab-panel{position:absolute;left:101px;top:832px;width:734px;height:225px;background:var(--panel);border:1px solid var(--panel-border)}
.panel-photo{position:absolute;left:27px;top:32px;width:233px;height:160px;background:linear-gradient(135deg,#e3e6ea,#f5f6f8 50%,#b9c0c8)}
.panel-copy{position:absolute;left:272px;top:28px;width:436px;font-size:10.5px;font-weight:300;line-height:18.7px;letter-spacing:-0.15px;color:#333}
.panel-copy p{margin-bottom:18.7px}
.site-footer{position:absolute;left:0;top:1112px;width:936px;height:88px;background:var(--footer);border-top:2px solid #2a2a2a;color:#fff}
.footer-nav{position:absolute;left:102px;top:22px;font-size:11.5px;font-weight:300}
.copyright{position:absolute;left:102px;top:51px;font-size:11.5px;font-weight:300}
.social{position:absolute;left:776px;top:32px;display:flex;gap:7px}
.social span{width:26px;height:26px;border-radius:50%}
.social .s1{background:#8cc3ea}
.social .s2{background:#5b78b9}
</style>
</head>
<body>
<header class="site-header">
  <div class="brand">KVR Inc</div>
  <div class="search">Search
    <svg width="10" height="10" viewBox="0 0 10 10"><circle cx="4" cy="4" r="3" fill="none" stroke="#555" stroke-width="1.2"/><line x1="6.2" y1="6.2" x2="9.4" y2="9.4" stroke="#555" stroke-width="1.5"/></svg>
  </div>
  <nav class="main-nav">Company | <span class="active">Products &amp; Services</span> | Learning Center | Events | KVR News | Contact Us</nav>
</header>

<section class="hero" role="img" aria-label="Scientist in safety glasses and blue gloves pipetting beside laboratory glassware"></section>
<div class="hero-dots"><span class="on"></span><span></span><span></span><span></span></div>

<h1 class="section-title">Instruments</h1>
<div class="section-sub">Bench Top Instruments</div>
<div class="pager">
  <svg width="19" height="19" viewBox="0 0 19 19"><circle cx="9.5" cy="9.5" r="9.5" fill="var(--dark-btn)"/><path d="M11 5.5 7 9.5 11 13.5" fill="none" stroke="#fff" stroke-width="2"/></svg>
  <svg width="19" height="19" viewBox="0 0 19 19"><circle cx="9.5" cy="9.5" r="9.5" fill="var(--dark-btn)"/><path d="M8 5.5 12 9.5 8 13.5" fill="none" stroke="#fff" stroke-width="2"/></svg>
</div>
<div class="section-rule"></div>

<div class="feature-photo" role="img" aria-label="Automated bench top liquid handling instrument with orange markings"></div>
<div class="feature-copy">
  <p>Maecenas imperdiet nisi eu justo dapibus, commodo venenatis massa tempus. Morbi consectetur sed justo vitae dictum. Ut semper tincidunt accumsan.</p>
  <p>Nunc suscipit dui in massa ultricies, ac sagittis velit pulvinar. In scelerisque id lectus eu facilisis. Morbi et nunc non nulla lobortis ultricies sit amet a turpis. Integer eget ullamcorper metus.</p>
  <p>Cras vitae nibh non dolor scelerisque porta.Nunc suscipit dui in massa ultricies, ac sagittis velit pulvinar... <a href="#">Read More</a></p>
</div>

<div class="tabs">
  <div class="tab current" style="left:0;width:118px">Overview</div>
  <div class="tab" style="left:125px;width:115px">Features</div>
  <div class="tab" style="left:246px;width:115px">Specifications</div>
  <div class="tab" style="left:370px;width:115px">FAQ’s</div>
  <div class="tab" style="left:494px;width:115px">Manuals</div>
</div>
<div class="tab-panel">
  <div class="panel-photo" role="img" aria-label="White compact bench top instrument with a small display"></div>
  <div class="panel-copy">
    <p>Donec nec ipsum eget erat lacinia consectetur. Sed non turpis pretium, porttitor lorem eu, congue turpis. Vivamus viverra semper sem eget elementum. Aliquam augue libero, hendrerit a tortor vestibulum, rutrum suscipit ante. Curabitur a ligula ligula. In eget eros non metus elementum consequat id quis enim.</p>
    <p>Vivamus dignissim pharetra mi a tempor. Aenean pellentesque, arcu sed sodales vestibulum, nunc nulla molestie sem, ut imperdiet neque turpis sed purus. Nunc euismod tortor nec nibh venenatis convallis. Suspendisse magna augue, blandit et quam ac, fermentum dignissim purus. Curabitur tempor ac metus ut bibendum.</p>
  </div>
</div>

<footer class="site-footer">
  <div class="footer-nav">Company | Products &amp; Services | Learning Center | Events | KVR News | Contact Us</div>
  <div class="copyright">Copyright ©2013 &nbsp;Company Name &nbsp;&nbsp;- All rights reserved</div>
  <div class="social"><span class="s1"></span><span class="s2"></span></div>
</footer>
</body>
</html>
```